Start-up braucht modernes/hochwertiges Getränkeetikett
Zielgruppe
Wir sind ein modernes, nachhaltiges Start-up, welches eine neue Getränkekategorie auf den Markt bringt. Ein sogenanntes Elektrolyt-Getränk mit dem Namen FLUXO4. Es ist abgefüllt in eine 500 ml Flasche und enthält Magnesium, Kalzium, Kalium, und Natrium. Diese Stoffe (Elektrolyte) dienen der körperlichen Hydrierung. Zu Dehydrierung kann es durch Hitze, Alkohol, Sport oder Krankheit kommen. Krankheit liegt bei uns allerdings nicht im Fokus. In unserer Zielgruppe befinden sich hauptsächlich Personen im Alter von 18 - 29 Jahren.
Die Geschmacksrichtung ist Zitrone-Limette.
Aufgabenstellung
Das Etikett soll:
- MODERN, SCHLICHT und HOCHWERTIG sein, so dass es im Supermarkt hervorsticht
- erkenntlich machen, dass die Stoffe Magnesium, Natrium, Kalzium und Kalium enthalten sind
- sich farblich deutlich von der Farbe des Inhalts (weiß) abheben. (Vorzugsweise mit einem hellen Blau, türkis)
- für unsere junge Zielgruppe ansprechend sein
- ebenfalls auf die Geschmacksrichtung (Zitrone-Limette) hinweisen, und zwar so, dass wenn man eine weitere Geschmacksrichtung auf den Markt bringen möchte, diese leicht angepasst werden kann.
- nicht nach einem Energydrink oder einem typischen Sportgetränk aussehen
- unter dem Namen den Slogan 'Elektrolyt-Getränk' stehen haben
-Das Etikett ist nicht dursichtig sondern besteht aus Papier
Der Name sowie das Logo können selbstverständlich farblich verändert werden. Bei dem Logo können auch größere Änderungen vollzogen werden.
Bitte beachten Sie die unten zu stehenden Regler um sich einen guten Überblick über unsere Vorstellungen zu verschaffen. Die Platzierung des EAN-Code ist für ihr Design irrelevat .
Bei Unklarheiten gerne nachfragen!

```html
<!DOCTYPE html>
<html lang="de">
<head>
<meta charset="utf-8">
<title>FLUXO4 Etikett</title>
<link href="https://fonts.googleapis.com/css2?family=Quicksand:wght@400;500;700&display=swap" rel="stylesheet">
<style>
  :root {
    --page-bg: #dcdde0;
    --teal-light: #a3dcd9;
    --teal-mid: #00b8a5;
    --teal-soft: #86d2c6;
    --teal-dusk: #8fb5b1;
    --blue-light: #9cc9e4;
    --blue-mid: #0a80b6;
    --blue-soft: #7db5d0;
    --strip-bg: #f4f5f5;
    --ink-dark: #27363f;
    --ink-grey: #56636b;
    --white: #ffffff;
  }
  * { margin: 0; padding: 0; box-sizing: border-box; }
  html, body {
    width: 667px; height: 1200px; overflow: hidden;
    background: var(--page-bg);
    font-family: "Quicksand", sans-serif;
  }
  .label {
    position: absolute; left: 23px; top: 117px;
    width: 620px; height: 965px;
    display: flex; flex-direction: column;
    overflow: hidden;
  }
  .label__hero {
    position: relative; height: 626px;
    background:
      radial-gradient(ellipse 60% 40% at 72% 8%, var(--teal-mid), transparent 70%),
      radial-gradient(ellipse 50% 50% at 50% 85%, #2f9f92, transparent 70%),
      linear-gradient(180deg, var(--teal-light) 0%, var(--teal-soft) 45%, var(--teal-dusk) 100%);
  }
  .brand-name {
    position: absolute; left: 56px; right: 68px; top: 64px;
    text-align: center; white-space: nowrap;
    font-weight: 700; font-size: 128px; line-height: 1;
    letter-spacing: -3px; color: var(--white);
  }
  .brand-claim {
    position: absolute; right: 72px; top: 200px;
    font-weight: 500; font-size: 28px; color: var(--ink-dark);
  }
  .brand-mark {
    position: absolute; left: 168px; top: 278px;
    width: 270px; height: 270px;
  }
  .label__strip {
    height: 47px; background: var(--strip-bg);
    display: flex; align-items: center; justify-content: center;
    font-size: 19px; font-weight: 500; color: var(--ink-grey);
    letter-spacing: -0.2px;
  }
  .label__strip .flavour { font-weight: 700; color: var(--ink-dark); }
  .label__minerals {
    height: 292px;
    background: linear-gradient(90deg, var(--blue-light) 0%, #5aa6d2 40%, var(--blue-mid) 68%, var(--blue-soft) 100%);
    display: flex; flex-direction: column; align-items: center; justify-content: center;
    gap: 4px;
  }
  .mineral {
    font-size: 42px; font-weight: 400; line-height: 51px;
    color: var(--white);
  }
  .mineral b { font-weight: 700; }
</style>
</head>
<body>
  <main class="label">
    <section class="label__hero">
      <h1 class="brand-name">FLUXO4</h1>
      <p class="brand-claim">Elektrolyt-Getränk</p>
      <svg class="brand-mark" viewBox="0 0 270 270" aria-label="FLUXO4">
        <circle cx="135" cy="135" r="128" fill="none" stroke="var(--white)" stroke-width="3"/>
        <text x="135" y="146" text-anchor="middle" fill="var(--white)"
              font-family="Quicksand, sans-serif" font-weight="700" font-size="34">FLUXO4</text>
      </svg>
    </section>
    <p class="label__strip">Dein wachmacher in&nbsp;<span class="flavour">Zitrone-Limette</span>&nbsp;geschmack</p>
    <section class="label__minerals">
      <p class="mineral"><b>Mag</b>nesium</p>
      <p class="mineral"><b>Na</b>trium</p>
      <p class="mineral"><b>Ca</b>lcium</p>
      <p class="mineral"><b>K</b>alium</p>
    </section>
  </main>
</body>
</html>
```